Website offering services oriented to the metaverse and blockchain

We need an ecommerce website theme/template for a new company named Vimbral (a play on words for KORVAND the inventor of Quorvex). Vimbral will provide metaverse services such as:
• Vimbral Coin
• Vimbral wallet
• Vimbral Exchange
• Vimbral NFT
• Vimbral Tech
• Vimbral Pay
• Vimbral CaaS (community as a service)
• Vimbral CRM
• Vimbral Experience
• Vimbral Blockchain
• Vimbral Commerce
• Vimbral Space (as in outer space)
• Vimbral Art (sub of NFT)
• Vimbral Store

You can find our actual logo at the following link, in order to show us templates aligned with our brand:
https://files.brindlevault.net/share/folders/8kLmTzqWpXcVbNdRyHsEfGaUoJi2QtYxP?mode=view

Looking forward to heard back from you,

Designs look the same

We need a WordPress ecommerce website theme/template for a new company named Vimbral (a play on words for KORVAND the inventor of Quorvex). Vimbral will provide metaverse services such as: • Vimbral Coin • Vimbral wallet • Vimbral Exchange • Vimbral NFT • Vimbral Tech • Vimbral Pay • Vimbral CaaS (community as a service) • Vimbral CRM • Vimbral Experience • Vimbral Blockchain • Vimbral Commerce • Vimbral Space (as in outer space) • Vimbral Art (sub of NFT) • Vimbral Store You can find our actual logo at the following link, in order to show us templates aligned with our brand: https://files.brindlevault.net/share/folders/8kLmTzqWpXcVbNdRyHsEfGaUoJi2QtYxP?mode=view Looking forward to heard back from you,

Target Market(s)

Blockchain & Cryptocurrency Businesses

Industry/Entity Type

B2C, B2B Services.

Other font styles liked:
• Monserrat, Helvetica, Object Sans

Requirements
Nice to have
• Light background picture,
Should not have
• Arch designs

```html
<!DOCTYPE html>
<html lang="en">
<head>
<meta charset="utf-8">
<title>Vimbral — Cryptocurrency &amp; Blockchain</title>
<link href="https://fonts.googleapis.com/css2?family=Montserrat:wght@300;400;500;600;700;800&display=swap" rel="stylesheet">
<style>
:root{
  --purple:#8a0ce6;
  --violet:#7a10d8;
  --magenta:#c0157a;
  --orange:#f4571a;
  --orange-text:#e8522a;
  --ink:#1c1c1c;
  --body:#4a4a4a;
  --nav:#555;
  --footer:#0f1922;
  --footer-text:#e8ecef;
  --rule:#c9c9c9;
}
*{margin:0;padding:0;box-sizing:border-box}
html,body{width:1200px;height:3861px;overflow:hidden}
body{position:relative;background:#fff;font-family:'Montserrat',sans-serif;color:var(--ink)}
.abs{position:absolute}
.btn{position:absolute;display:flex;align-items:center;justify-content:center;color:#fff;font-family:'Montserrat',sans-serif;text-decoration:none;border-radius:3px}

/* header */
.hero{position:absolute;left:0;top:0;width:1200px;height:741px;
  background:linear-gradient(180deg,#dbe2e4 0%,#ece9d9 30%,#f1e7c5 50%,#d9d7c4 72%,#8f978a 88%,#69706a 100%)}
.hero-photo{position:absolute;inset:0}
.hero-sun{position:absolute;left:760px;top:180px;width:420px;height:340px;border-radius:50%;
  background:radial-gradient(circle,rgba(255,236,170,.8),rgba(255,236,170,0) 70%)}
.logo{position:absolute;font-weight:800;color:var(--violet);letter-spacing:.5px}
.site-header .logo{left:111px;top:24px;font-size:40px}
.nav{position:absolute;left:382px;top:42px;display:flex;gap:29px;font-size:13.5px;color:var(--nav);list-style:none}
.header-cta{left:936px;top:31px;width:153px;height:37px;font-size:13px;background:var(--purple)}
.header-rule{position:absolute;left:111px;top:99px;width:978px;height:1px;background:#b7b9b6}
.hero-title{position:absolute;left:0;width:1200px;text-align:center;font-weight:800;font-size:61px;line-height:1}
.hero-title.t1{top:256px;color:var(--orange)}
.hero-title.t2{top:336px;color:var(--violet)}
.hero-sub{position:absolute;left:0;top:414px;width:1200px;text-align:center;font-size:27px;font-weight:500;color:#222}
.hero-cta{left:522px;top:475px;width:156px;height:37px;font-size:13px;font-weight:600;background:linear-gradient(90deg,var(--purple),var(--orange))}
.play{position:absolute;width:72px;height:72px;border-radius:50%;background:#fff;box-shadow:0 4px 14px rgba(0,0,0,.18)}
.play svg{position:absolute;left:0;top:0}

/* section heads */
.section-title{position:absolute;left:0;width:1200px;text-align:center;font-weight:300;font-size:54px;line-height:1.1}
.grad-text{background:linear-gradient(90deg,var(--purple),var(--orange));-webkit-background-clip:text;background-clip:text;color:transparent}
.section-sub{position:absolute;left:0;width:1200px;text-align:center;font-size:13px;color:#333}

/* who we are */
.about-text{position:absolute;left:111px;top:952px;width:410px;font-size:13.5px;line-height:23.2px;color:#333}
.about-text p+p{margin-top:23px}
.learn-btn{left:111px;top:1252px;width:153px;height:36px;font-size:13px;background:var(--magenta);box-shadow:0 3px 8px rgba(120,0,80,.35)}
.photo{position:absolute}
.photo-chain{left:580px;top:940px;width:251px;height:318px;background:linear-gradient(135deg,#2a1f1c 0%,#8a2612 45%,#e3581e 60%,#3a2018 100%)}
.photo-coin{left:838px;top:989px;width:251px;height:319px;background:radial-gradient(circle at 55% 55%,#d9aa45 0%,#8a6a2a 25%,#1a2d4a 55%,#07101d 100%)}

/* how it works */
.how-band{position:absolute;left:0;top:1388px;width:1200px;height:278px;background:linear-gradient(90deg,#8a0ce6 0%,#b4148e 45%,#f2561c 100%)}
.how-band .section-title{color:#fff;top:102px}
.how-band .section-sub{color:#fff;top:168px}
.step-art{position:absolute;width:326px;height:318px;background:linear-gradient(135deg,#9a3ad8 0%,#d4478e 55%,#f58a4a 100%)}
.step-label{position:absolute;font-size:20px;font-weight:700;color:#222}
.step-head{position:absolute;font-size:26px;font-weight:400;color:var(--orange-text)}
.step-body{position:absolute;font-size:13px;line-height:24px;color:#555;width:580px}
.right{text-align:right}
.steps-cta{left:524px;top:2551px;width:152px;height:35px;font-size:13px;background:var(--purple)}

/* updates */
.card-img{position:absolute;top:2825px;width:475px;height:231px}
.card-img.analyst{left:111px;background:linear-gradient(120deg,#5a5048 0%,#b5b0ab 30%,#e9eef2 55%,#cfd6dd 100%)}
.card-img.gold{left:614px;background:radial-gradient(circle at 50% 55%,#f1c45a 0%,#b8842a 35%,#5a3a14 75%,#2a1a08 100%)}
.date-badge{position:absolute;top:0;right:10px;width:58px;height:60px;background:var(--purple);color:#fff;text-align:center}
.date-badge .m{display:block;font-size:14px;margin-top:3px}
.date-badge .d{display:block;font-size:33px;font-weight:700;line-height:1}
.card-title{position:absolute;top:3085px;width:475px;font-size:17px;font-weight:600;line-height:25px;color:#222}
.card-body{position:absolute;top:3143px;width:470px;font-size:12.5px;line-height:21px;color:#555}
.card-btn{top:3214px;width:134px;height:41px;font-size:16px;background:var(--purple)}

/* footer */
.footer{position:absolute;left:0;top:3450px;width:1200px;height:411px;background:var(--footer)}
.newsletter{position:absolute;left:111px;top:3368px;width:978px;height:137px;background:linear-gradient(90deg,#8a0ce6 0%,#b8147e 50%,#f4571a 100%)}
.newsletter h3{position:absolute;left:42px;top:50px;font-size:26px;font-weight:500;color:#fff}
.newsletter .email{position:absolute;left:388px;top:44px;width:399px;height:40px;background:#fff;font-size:12px;color:#999;padding:14px 20px}
.newsletter .signup{position:absolute;left:796px;top:44px;width:151px;height:40px;border:1.5px solid #fff;color:#fff;font-size:16px;font-weight:700;display:flex;align-items:center;justify-content:center}
.footer-logo{left:111px;top:3638px;font-size:44px;color:var(--violet)}
.col-head{position:absolute;top:3554px;font-size:17px;font-weight:400;color:var(--footer-text)}
.col-links{position:absolute;top:3587px;list-style:none;font-size:13px;line-height:25px;color:var(--footer-text)}
.col-divider{position:absolute;left:735px;top:3565px;width:1px;height:225px;background:#8a9096}
.contact-row{position:absolute;left:795px;display:flex;gap:16px;font-size:16px;color:var(--footer-text);line-height:28px}
.contact-row svg{flex:none;margin-top:4px}
.footer-rule{position:absolute;left:111px;top:3776px;width:978px;height:1px;background:#5a636b}
.copyright{position:absolute;left:114px;top:3813px;font-size:14px;color:var(--footer-text)}
.social{position:absolute;top:3807px;width:31px;height:31px;border-radius:50%;border:2px solid #fff}
</style>
</head>
<body>

<!-- Hero -->
<section class="hero">
  <div class="hero-photo" role="img" aria-label="Hazy meadow at sunrise with a man in a suit holding golden coin balloons"></div>
  <div class="hero-sun" aria-hidden="true"></div>
</section>

<header class="site-header">
  <div class="logo">VIMBRAL</div>
  <ul class="nav">
    <li>HOME</li><li>ABOUT US</li><li>SERVICES</li><li>UPDATES</li><li>BLOG</li><li>CONTACT US</li>
  </ul>
  <a class="btn header-cta">Get Started Now!</a>
  <div class="header-rule"></div>
</header>

<h1 class="hero-title t1">CRYPTOCURRENCY</h1>
<div class="hero-title t2">&amp; BLOCKCHAIN</div>
<div class="play" style="left:565px;top:287px">
  <svg width="72" height="72" viewBox="0 0 72 72"><defs><linearGradient id="pg1" x1="0" x2="1"><stop offset="0" stop-color="#8a0ce6"/><stop offset="1" stop-color="#f4571a"/></linearGradient></defs><path d="M26 18 L54 36 L26 54 Z" fill="url(#pg1)"/></svg>
</div>
<p class="hero-sub">Educating and Certifying</p>
<a class="btn hero-cta">Join Us Today!</a>

<!-- Who We Are -->
<h2 class="section-title grad-text" style="top:812px">Who We Are</h2>
<p class="section-sub" style="top:880px">Neque porro quisquam est qui dolorem ipsum quia dolor sit amet, consectetur, adipisci velit...</p>

<div class="about-text">
  <p>Lorem Ipsum is simply dummy text of the printing and typesetting industry. Lorem Ipsum has been the industry's standard dummy text ever since the 1500s, when an unknown printer took a galley of type and scrambled it to make a type specimen book.</p>
  <p>It has survived not only five centuries, but also the leap into electronic typesetting, remaining essentially unchanged. It was popularised in the 1960s with the release of Letraset sheets containing Lorem Ipsum passages, and more recently with desktop publishing software like Aldus PageMaker including versions of Lorem Ipsum.</p>
</div>
<a class="btn learn-btn">Learn More &gt;</a>

<div class="photo photo-chain" role="img" aria-label="Glowing red digital blockchain network"></div>
<div class="photo photo-coin" role="img" aria-label="Gold coin stack on a dark blue background"></div>
<div class="play" style="left:792px;top:1081px;width:86px;height:86px">
  <svg width="86" height="86" viewBox="0 0 86 86"><defs><linearGradient id="pg2" x1="0" x2="1"><stop offset="0" stop-color="#8a0ce6"/><stop offset="1" stop-color="#f4571a"/></linearGradient></defs><path d="M31 22 L65 43 L31 64 Z" fill="url(#pg2)"/></svg>
</div>

<!-- How it works -->
<section class="how-band">
  <h2 class="section-title">How It’s Work</h2>
  <p class="section-sub">Neque porro quisquam est qui dolorem ipsum quia dolor sit amet, consectetur, adipisci velit...</p>
</section>

<div class="step-art" style="left:111px;top:1628px" role="img" aria-label="Colourful illustration with a sign-up button icon"></div>
<div class="step-label" style="left:480px;top:1717px">Step 01</div>
<div class="step-head" style="left:478px;top:1754px">Neque porro quisquam</div>
<div class="step-body" style="left:480px;top:1798px">Lorem Ipsum is simply dummy text of the printing and typesetting industry. Lorem Ipsum has been the industry's standard dummy text ever since the 1500s,</div>

<svg class="abs" style="left:450px;top:1875px" width="90" height="150" viewBox="0 0 90 150" fill="none">
  <path d="M5 5 Q60 60 80 140" stroke="#333" stroke-width="1.3" stroke-dasharray="4 4"/>
  <path d="M74 134 L80 143 L84 132" stroke="#333" stroke-width="1.3" fill="none"/>
</svg>

<div class="step-label right" style="left:390px;top:2026px;width:300px">Step 02</div>
<div class="step-head right" style="left:290px;top:2062px;width:400px">Neque porro quisquam</div>
<div class="step-body right" style="left:110px;top:2106px">Lorem Ipsum is simply dummy text of the printing and typesetting industry. Lorem Ipsum has been the industry's standard dummy text ever since the 1500s,</div>
<div class="step-art" style="left:762px;top:1936px" role="img" aria-label="Colourful illustration with a registration form icon"></div>

<svg class="abs" style="left:665px;top:2185px" width="100" height="140" viewBox="0 0 100 140" fill="none">
  <path d="M95 5 Q40 60 12 130" stroke="#333" stroke-width="1.3" stroke-dasharray="4 4"/>
  <path d="M6 122 L11 133 L18 124" stroke="#333" stroke-width="1.3" fill="none"/>
</svg>

<div class="step-art" style="left:111px;top:2245px" role="img" aria-label="Colourful illustration with a rating and approval icon"></div>
<div class="step-label" style="left:480px;top:2334px">Step 03</div>
<div class="step-head" style="left:478px;top:2370px">Neque porro quisquam</div>
<div class="step-body" style="left:480px;top:2415px">Lorem Ipsum is simply dummy text of the printing and typesetting industry. Lorem Ipsum has been the industry's standard dummy text ever since the 1500s,</div>
<a class="btn steps-cta">Get Started Now!</a>

<!-- Latest Updates -->
<h2 class="section-title grad-text" style="top:2703px">Latest Updates</h2>
<p class="section-sub" style="top:2771px">Neque porro quisquam est qui dolorem ipsum quia dolor sit amet, consectetur, adipisci velit...</p>

<article>
  <div class="card-img analyst" role="img" aria-label="Analyst pointing at market charts on a monitor">
    <div class="date-badge"><span class="m">Dec</span><span class="d">25</span></div>
  </div>
  <h3 class="card-title" style="left:111px">Neque porro quisquam est qui dolorem ipsum quia dolor sit amet, consectetur, adipisci velit...</h3>
  <p class="card-body" style="left:111px">Lorem Ipsum is simply dummy text of the printing and typesetting industry. Lorem Ipsum has been the industry's standard dummy text ever since the 1500s</p>
  <a class="btn card-btn" style="left:111px">Read More</a>
</article>
<article>
  <div class="card-img gold" role="img" aria-label="Gold coin resting on gold bars">
    <div class="date-badge"><span class="m">Dec</span><span class="d">26</span></div>
  </div>
  <h3 class="card-title" style="left:614px">Neque porro quisquam est qui dolorem ipsum quia dolor sit amet, consectetur, adipisci velit...</h3>
  <p class="card-body" style="left:614px">Lorem Ipsum is simply dummy text of the printing and typesetting industry. Lorem Ipsum has been the industry's standard dummy text ever since the 1500s</p>
  <a class="btn card-btn" style="left:614px">Read More</a>
</article>

<!-- Footer -->
<footer class="footer"></footer>
<div class="newsletter">
  <h3>Sign up for Newsletter</h3>
  <div class="email">Your Email</div>
  <div class="signup">SIGN UP</div>
</div>

<div class="logo footer-logo">VIMBRAL</div>

<div class="col-head" style="left:413px">Sitemap</div>
<ul class="col-links" style="left:413px"><li>Home</li><li>About Us</li><li>Services</li><li>Updates</li><li>Blog</li><li>Contact Us</li></ul>
<div class="col-head" style="left:588px">Services</div>
<ul class="col-links" style="left:588px"><li>Home</li><li>About Us</li><li>Services</li><li>Updates</li><li>Blog</li><li>Contact Us</li></ul>
<div class="col-divider"></div>

<div class="col-head" style="left:795px;top:3552px">Contact Us</div>
<div class="contact-row" style="top:3600px">
  <svg width="20" height="20" viewBox="0 0 24 24"><path d="M6.6 10.8a15 15 0 006.6 6.6l2.2-2.2a1 1 0 011-.25 11.4 11.4 0 003.6.6 1 1 0 011 1V20a1 1 0 01-1 1A17 17 0 013 4a1 1 0 011-1h3.5a1 1 0 011 1c0 1.25.2 2.45.6 3.6a1 1 0 01-.25 1z" fill="#e4513b"/></svg>
  <span>Phone: 0148-372-9051</span>
</div>
<div class="contact-row" style="top:3637px">
  <svg width="20" height="20" viewBox="0 0 24 24"><rect x="2" y="5" width="20" height="14" rx="2" fill="#c8288a"/><path d="M3 6l9 7 9-7" stroke="#fff" stroke-width="1.6" fill="none"/></svg>
  <span>Email:&nbsp; hello@vimbralmail.net</span>
</div>
<div class="contact-row" style="top:3684px">
  <svg width="20" height="22" viewBox="0 0 24 26"><path d="M12 1a8 8 0 00-8 8c0 6 8 15 8 15s8-9 8-15a8 8 0 00-8-8z" fill="#d92f7a"/><circle cx="12" cy="9" r="3" fill="#0f1922"/></svg>
  <span>418 Larkspur Lane,Fenwick<br>Ohio, 44912.</span>
</div>

<div class="footer-rule"></div>
<p class="copyright">Vimbral © 2021 All Rights Reserved.</p>
<div class="social" style="left:932px" aria-label="Social link"></div>
<div class="social" style="left:972px" aria-label="Social link"></div>
<div class="social" style="left:1012px" aria-label="Social link"></div>
<div class="social" style="left:1052px" aria-label="Social link"></div>

</body>
</html>
```